CPA Firm Stationary & Business Cards
Whitford & Partners CPAs PSC
CPA Firm Stationary & Business Cards - Financial Services
Creative Brief
Professional
Martin L. Pradley, CPA
Shareholder
5814 Ellsworth Ave. Suite 1 Cedarbrook, KY 41876
mpradley@wpfcpa.example
www.wpfcpa.example
We are a CPA (Certified Public Accountant) firm, in business since 1924. In addition to Business Cards, I would also like to see designs for Letterheads and Envelopes.
Your choice. At a minimum, it should include the "W" logo.In addition to Business Cards, I would also like to see designs for Letterheads and Envelopes.

```html
<!DOCTYPE html>
<html lang="en">
<head>
<meta charset="utf-8">
<title>Whitford &amp; Partners CPAs PSC – Business Card</title>
<link href="https://fonts.googleapis.com/css2?family=Montserrat:wght@400;500;600;700&display=swap" rel="stylesheet">
<style>
  :root{
    --page:#e8ebf0;
    --white:#ffffff;
    --navy:#15307f;
    --blue:#2359c4;
    --sky:#3f8be6;
    --ink:#2b3445;
    --muted:#6b7587;
  }
  *{box-sizing:border-box;margin:0;padding:0}
  html,body{width:1200px;height:1060px;overflow:hidden}
  body{
    background:var(--page);
    font-family:"Montserrat",Arial,sans-serif;
    display:flex;flex-direction:column;align-items:center;justify-content:center;gap:40px;
  }
  .card{
    position:relative;width:840px;height:480px;border-radius:22px;overflow:hidden;
    box-shadow:0 10px 30px rgba(20,40,90,.18);
  }
  .card--details{background:var(--white)}
  .card__band{position:absolute;inset:0}
  .phones{
    position:absolute;left:38px;top:170px;color:var(--white);
    font-size:17px;font-weight:500;display:flex;flex-direction:column;gap:22px;
  }
  .phones li,.contact li{list-style:none;display:flex;align-items:center;gap:12px;white-space:nowrap}
  .phones svg{width:18px;height:18px;fill:var(--white)}
  .wordmark{
    color:var(--navy);font-weight:600;text-transform:uppercase;line-height:1;
    display:flex;align-items:center;gap:14px;
  }
  .wordmark__dot{width:22px;height:22px;border-radius:50%;background:var(--navy);flex:none}
  .wordmark__name{display:block;font-size:46px;letter-spacing:2px}
  .wordmark__sub{display:block;font-size:19px;letter-spacing:1.5px;margin-top:8px}
  .card--details .wordmark{position:absolute;right:48px;top:56px}
  .person{position:absolute;left:400px;top:228px}
  .person__name{font-size:26px;font-weight:700;color:var(--blue)}
  .person__title{font-size:16px;font-weight:500;color:var(--muted);margin-top:4px;font-style:italic}
  .contact{
    position:absolute;left:400px;top:318px;color:var(--ink);font-size:15px;
    display:flex;flex-direction:column;gap:12px;
  }
  .contact svg{width:16px;height:16px;fill:var(--blue);flex:none}
  .card--brand{
    background:linear-gradient(160deg,var(--navy) 0%,var(--blue) 55%,var(--sky) 100%);
  }
  .card--brand .wordmark{position:absolute;left:90px;top:170px;color:var(--white)}
  .card--brand .wordmark__dot{background:var(--white);width:30px;height:30px}
  .card--brand .wordmark__name{font-size:64px}
  .card--brand .wordmark__sub{font-size:26px;margin-top:12px}
</style>
</head>
<body>

<section class="card card--details" aria-label="Business card, contact side">
  <svg class="card__band" viewBox="0 0 840 480" width="840" height="480" aria-hidden="true">
    <defs>
      <linearGradient id="bandFill" x1="0" y1="0" x2="1" y2="1">
        <stop offset="0" stop-color="#15307f"/>
        <stop offset="1" stop-color="#3f8be6"/>
      </linearGradient>
    </defs>
    <path d="M0 0 H330 C250 140 250 330 360 480 H0 Z" fill="#cfe0f7"/>
    <path d="M0 0 H305 C225 140 225 330 335 480 H0 Z" fill="url(#bandFill)"/>
  </svg>

  <ul class="phones">
    <li><svg viewBox="0 0 24 24"><path d="M6.6 10.8a15.1 15.1 0 0 0 6.6 6.6l2.2-2.2a1 1 0 0 1 1-.25 11.4 11.4 0 0 0 3.6.57 1 1 0 0 1 1 1V20a1 1 0 0 1-1 1A17 17 0 0 1 3 4a1 1 0 0 1 1-1h3.5a1 1 0 0 1 1 1c0 1.25.2 2.45.57 3.6a1 1 0 0 1-.25 1z"/></svg>T 555-014-2236</li>
    <li><svg viewBox="0 0 24 24"><path d="M19 8H5a3 3 0 0 0-3 3v6h4v4h12v-4h4v-6a3 3 0 0 0-3-3zm-3 11H8v-5h8zm3-16H5v4h14z"/></svg>F 555-018-7741</li>
  </ul>

  <div class="wordmark">
    <span class="wordmark__dot"></span>
    <span><span class="wordmark__name">Whitford</span><span class="wordmark__sub">&amp; Partners CPAs PSC</span></span>
  </div>

  <div class="person">
    <p class="person__name">Martin L. Pradley, CPA</p>
    <p class="person__title">Shareholder</p>
  </div>

  <ul class="contact">
    <li><svg viewBox="0 0 24 24"><path d="M12 2a7 7 0 0 0-7 7c0 5.2 7 13 7 13s7-7.8 7-13a7 7 0 0 0-7-7zm0 9.5A2.5 2.5 0 1 1 12 6.5a2.5 2.5 0 0 1 0 5z"/></svg>5814 Ellsworth Ave. Suite 1 | Cedarbrook, KY 41876</li>
    <li><svg viewBox="0 0 24 24"><path d="M20 4H4a2 2 0 0 0-2 2v12a2 2 0 0 0 2 2h16a2 2 0 0 0 2-2V6a2 2 0 0 0-2-2zm0 4-8 5-8-5V6l8 5 8-5z"/></svg>mpradley@wpfcpa.example</li>
    <li><svg viewBox="0 0 24 24"><path d="M12 2a10 10 0 1 0 0 20 10 10 0 0 0 0-20zm6.9 6h-2.9a15.7 15.7 0 0 0-1.4-3.6A8 8 0 0 1 18.9 8zM12 4c.8 1.2 1.5 2.5 1.9 4h-3.8c.4-1.5 1.1-2.8 1.9-4zM4.3 14a8.2 8.2 0 0 1 0-4h3.4a16 16 0 0 0 0 4zm.8 2h2.9c.3 1.3.8 2.5 1.4 3.6A8 8 0 0 1 5.1 16zM8 8H5.1a8 8 0 0 1 4.3-3.6C8.8 5.5 8.3 6.7 8 8zm4 12c-.8-1.2-1.5-2.5-1.9-4h3.8c-.4 1.5-1.1 2.8-1.9 4zm2.3-6H9.7a14.7 14.7 0 0 1 0-4h4.6a14.7 14.7 0 0 1 0 4zm.3 5.6c.6-1.1 1.1-2.3 1.4-3.6h2.9a8 8 0 0 1-4.3 3.6zM16.3 14a16 16 0 0 0 0-4h3.4a8.2 8.2 0 0 1 0 4z"/></svg>www.wpfcpa.example</li>
  </ul>
</section>

<section class="card card--brand" aria-label="Business card, brand side">
  <div class="wordmark">
    <span class="wordmark__dot"></span>
    <span><span class="wordmark__name">Whitford</span><span class="wordmark__sub">&amp; Partners CPAs PSC</span></span>
  </div>
</section>

</body>
</html>
```